kolvarin.link kolvarin.space kolvarin.press website

The website is named KOLVARIN and it will have 3 domain names. kolvarin.link, press, space.
I'd like it to be viewed on Pads, pcs and phones.

page menu:

kolvarin.link(start page): presentation of company. (creative, design, app, new product innovation.)
Here we'll need sosial media icons: plimber, vendoloop, mirtavel, trelvanet. (light but some 'fruity' colors)

kolvarin.press: blog. It will be a 75% picture blog > rest will be text. I need to be able to resize pictures and shape columns to picture size. (light but some 'fruity' colors)

kolvarin.space : the fun part of this web design, however, on entering the page I'd like a non-disclosure agreement where viewer simply click "yes, I agree" after filling out contact info. (check attached document)
We will have space here for uploading PDF files viewers can download. There is also a blog space here to tell in brief about the PDF file. (maybe a space/sci-fi theme her e.g spacechimp, Laika the space dog?)

I will attach the logo here I want you to use > and develop for the .space .press webpage. The logo i uploaded is for the .link page.

Target Market(s)

venture capitalists

Number of Pages Required

3 page

Requirements
Must have
• a few 'fruity colors' but mostly white and grey

```html
<!DOCTYPE html>
<html lang="en">
<head>
<meta charset="utf-8">
<title>Kolvarin — Mobile App</title>
<link rel="stylesheet" href="https://fonts.googleapis.com/css2?family=Silkscreen:wght@400;700&family=Open+Sans:ital,wght@0,400;0,600;0,700;1,400&display=swap">
<style>
:root{
  --green:#8cc63f;
  --green-dark:#7ab52f;
  --mustard:#c8922a;
  --coral:#e9553c;
  --rust:#c64a1d;
  --ink:#2b2b2b;
  --text:#555;
  --muted:#888;
  --white:#fff;
  --leaf:#2e8b3e;
  --line:#e2e2e2;
  --pixel:"Silkscreen", monospace;
  --body:"Open Sans", sans-serif;
}
*{box-sizing:border-box;margin:0;padding:0}
html,body{width:1200px;height:3056px;overflow:hidden}
body{font-family:var(--body);color:var(--text);background:var(--white);position:relative}
section,header,footer{position:relative;width:1200px;overflow:hidden}
.abs{position:absolute}
.btn{position:absolute;display:flex;align-items:center;justify-content:center;font:600 15px/1 var(--body);color:var(--white);text-transform:uppercase;border-radius:3px}
.btn--ghost{border:2px solid var(--white)}
.btn--solid{background:var(--coral)}
.pixel{font-family:var(--pixel);font-weight:700;text-transform:uppercase;letter-spacing:2px}

/* hero */
.hero{height:625px;background:var(--green)}
.brand{left:98px;top:36px;display:flex;align-items:center;gap:12px}
.brand__mark{width:30px;height:30px;background:var(--coral)}
.brand__name{font:700 30px/1 var(--pixel);color:var(--ink)}
.nav{left:560px;top:50px;display:flex;gap:0}
.nav a{font:600 14px/1 var(--body);color:var(--white);text-decoration:none;text-transform:uppercase;margin-right:40px;padding-top:10px}
.nav__cta{left:947px;top:43px;width:153px;height:34px;font-size:13px}
.hero__title{left:214px;top:240px;color:var(--white)}
.hero__title span{display:block}
.hero__title .l1{font-size:44px;line-height:48px}
.hero__title .l2{font-size:56px;line-height:60px}
.hero__lead{left:214px;top:356px;width:440px;font:600 13px/21px var(--body);color:#f4fbe9}
.hero__dl{left:218px;top:444px;width:165px;height:45px}
.hero__more{left:403px;top:444px;width:163px;height:45px}
.dots{left:216px;top:526px;display:flex;gap:12px}
.dots i{width:15px;height:15px;border-radius:50%;border:2px solid #cde7a8}
.dots i.on{background:var(--coral);border-color:var(--coral)}
.hero__device{left:723px;top:153px;width:255px;height:413px;border-radius:36px;background:linear-gradient(160deg,#ffffff,#dcdcdc);box-shadow:14px 10px 0 #2f3a2a}
.hero__arrow{top:588px}

/* features */
.features{height:618px}
.sec-title{position:absolute;left:0;width:1200px;text-align:center;color:var(--ink);font-size:31px}
.divider{position:absolute;left:500px;width:200px;height:1px;background:var(--line)}
.sec-lead{position:absolute;left:300px;width:600px;text-align:center;font:11px/22px var(--body);color:var(--muted)}
.features__hand{left:173px;top:210px;width:326px;height:408px;background:linear-gradient(180deg,#f5f5f5 0%,#e8c3a6 55%,#d9a583 100%);border-radius:60px 60px 0 0}
.feature{position:absolute;left:562px;width:430px;display:flex;gap:33px}
.feature__icon{flex:none;width:54px;height:58px;border-radius:12px;display:flex;align-items:center;justify-content:center}
.feature__icon--orange{background:#f79b1c}
.feature__icon--red{background:#e83b2a}
.feature__icon--yellow{background:#f2cc1b}
.feature h3{font:400 19px/24px var(--body);color:var(--ink);margin-bottom:6px}
.feature p{font:11px/20px var(--body);color:var(--text)}

/* share */
.share{height:444px;background:var(--mustard)}
.share__title{left:0;width:1200px;text-align:center;color:var(--white);top:105px}
.share__title .l1{display:block;font-size:50px;line-height:56px}
.share__title .l2{display:block;font-size:30px;line-height:36px}
.share__lead{left:300px;top:214px;width:600px;text-align:center;font:600 13px/21px var(--body);color:#fbeed5}
.share__dl{left:424px;top:293px;width:167px;height:47px}
.share__more{left:607px;top:293px;width:167px;height:47px}

/* innovation */
.innovation{height:476px}
.innovation__photo{left:108px;top:77px;width:432px;height:330px;border:8px solid #ececec;background:linear-gradient(135deg,#dfe3e3 0%,#f2f2f0 45%,#c9c9c4 100%)}
.innovation__title{left:580px;top:94px;font-size:31px;color:var(--ink)}
.innovation__sub{left:580px;top:140px;font:400 18px/24px var(--body);color:var(--ink)}
.innovation__text{left:580px;top:176px;width:510px;font:11px/21px var(--body);color:var(--text)}
.checks{left:580px;top:290px;list-style:none}
.checks li{font:12px/26px var(--body);color:var(--text);display:flex;align-items:center;gap:10px}
.checks li::before{content:"✓";width:12px;height:12px;background:#d7332a;color:var(--white);font-size:9px;line-height:12px;text-align:center;border-radius:2px}

/* notify */
.notify{height:395px;background:var(--green)}
.notify__title{left:0;width:1200px;text-align:center;top:82px;color:var(--white);font-size:40px}
.notify__lead{left:300px;top:150px;width:600px;text-align:center;font:600 13px/21px var(--body);color:#f4fbe9}
.notify__field{left:330px;top:206px;width:540px;height:57px;background:var(--white);display:flex;align-items:center;padding-left:20px;gap:20px;font:15px var(--body);color:#bbb}
.notify__btn{left:519px;top:281px;width:163px;height:45px}

/* reviews */
.reviews{height:345px}
.reviews__title{top:70px;font-size:31px}
.reviews__title em{font-style:normal;color:var(--leaf)}
.review{position:absolute;top:151px;display:flex;gap:14px}
.review__avatar{flex:none;width:122px;height:122px;border-radius:50%;background:radial-gradient(circle at 50% 40%,#c9d6e2,#7f95ab);border:4px solid #eee}
.review__body{width:380px;padding-top:8px}
.review__body q{font:italic 11px/20px var(--body);color:var(--text);quotes:"\201C" "\201D"}
.review__stars{margin-top:8px;color:#f0a81e;font-size:10px;letter-spacing:1px}
.review__stars span{color:#ccc}
.review__name{margin-top:6px;font:italic 12px var(--body);color:var(--leaf)}

/* footer */
.footer{height:153px;background:var(--rust)}
.social{left:515px;top:22px;display:flex;gap:6px}
.social i{width:38px;height:38px;border-radius:6px;background:#f4a21c}
.footer__nav{left:0;width:1200px;top:74px;text-align:center;font:600 11px var(--body);color:var(--white);text-transform:uppercase;word-spacing:4px}
.footer__copy{left:0;width:1200px;top:102px;text-align:center;font:12px var(--body);color:#fbe3d6}
</style>
</head>
<body>

<header class="hero">
  <div class="abs brand"><span class="brand__mark"></span><span class="brand__name">KOLVARIN</span></div>
  <nav class="abs nav"><a>Home</a><a>Product</a><a>Help</a><a>Contact Us</a></nav>
  <a class="btn btn--solid nav__cta">Download App</a>

  <h1 class="abs hero__title pixel"><span class="l1">Kolvarin</span><span class="l2">Mobile App</span></h1>
  <p class="abs hero__lead">Duis sed odio sit amet nibh vulputate cursus a sit amet mauris. Morbi accumsan ipsum velit. Nam nec tellus a odio tincidunt auctor a ornare odio. Sed non mauris vitae erat consequat auctor.</p>
  <a class="btn btn--ghost hero__dl">Download</a>
  <a class="btn btn--solid hero__more">Learn More</a>
  <div class="abs dots"><i class="on"></i><i></i><i></i></div>

  <div class="abs hero__device" role="img" aria-label="Smartphone showing the app's fruit tile grid and a download button"></div>

  <svg class="abs hero__arrow" style="left:12px" width="14" height="20" viewBox="0 0 14 20"><path d="M11 2 3 10l8 8" fill="none" stroke="#b9dd87" stroke-width="3"/></svg>
  <svg class="abs hero__arrow" style="left:1090px" width="14" height="20" viewBox="0 0 14 20"><path d="M3 2l8 8-8 8" fill="none" stroke="#b9dd87" stroke-width="3"/></svg>
</header>

<section class="features">
  <h2 class="sec-title pixel" style="top:66px">Product Features</h2>
  <span class="divider" style="top:104px"></span>
  <p class="sec-lead" style="top:120px">Sed ut perspiciatis unde omnis iste natus error sit voluptatem accusantium doloremque laudantium, totam rem aperiam, eaque ipsa quae ab illo inventore veritatis et quasi architecto.</p>

  <div class="abs features__hand" role="img" aria-label="Hand holding a phone with the install screen"></div>

  <div class="feature" style="top:210px">
    <span class="feature__icon feature__icon--orange">
      <svg width="18" height="28" viewBox="0 0 18 28"><rect x="1.5" y="1.5" width="15" height="25" rx="3" fill="none" stroke="#fff" stroke-width="2.5"/><circle cx="9" cy="22" r="1.5" fill="#fff"/></svg>
    </span>
    <div><h3>Order from phone</h3><p>Lorem ipsum dolor sit amet, consectetur adipiscing elit, sed do eiusmod tempor incididunt ut labore et dolore magna</p></div>
  </div>
  <div class="feature" style="top:318px">
    <span class="feature__icon feature__icon--red">
      <svg width="28" height="28" viewBox="0 0 28 28"><circle cx="14" cy="14" r="11" fill="none" stroke="#fff" stroke-width="3"/><circle cx="14" cy="14" r="5" fill="none" stroke="#fff" stroke-width="3"/></svg>
    </span>
    <div><h3>Nemo enim ipsam volupt</h3><p>Lorem ipsum dolor sit amet, consectetur adipiscing elit, sed do eiusmod tempor incididunt ut labore et dolore magna</p></div>
  </div>
  <div class="feature" style="top:428px">
    <span class="feature__icon feature__icon--yellow">
      <svg width="28" height="24" viewBox="0 0 28 24"><path d="M3 20a11 11 0 1 1 22 0" fill="none" stroke="#fff" stroke-width="3"/><path d="M14 20l5-7" stroke="#fff" stroke-width="3"/></svg>
    </span>
    <div><h3>Quis autem vel eum</h3><p>Lorem ipsum dolor sit amet, consectetur adipiscing elit, sed do eiusmod tempor incididunt ut labore et dolore magna</p></div>
  </div>
</section>

<section class="share">
  <h2 class="abs share__title pixel"><span class="l1">Share Your Favorite</span><span class="l2">Mobile Apps With Your Friends</span></h2>
  <p class="abs share__lead">Duis sed odio sit amet nibh vulputate cursus a sit amet mauris. Morbi accumsan ipsum velit. Nam nec tellus a odio tincidunt auctor a ornare odio. Sed non mauris</p>
  <a class="btn btn--ghost share__dl">Download</a>
  <a class="btn btn--solid share__more">Learn More</a>
</section>

<section class="innovation">
  <div class="abs innovation__photo" role="img" aria-label="Hand using the app on a phone above a white keyboard"></div>
  <h2 class="abs innovation__title pixel">New Product Innovation</h2>
  <p class="abs innovation__sub">Duis aute irure dolor in reprehenderit</p>
  <p class="abs innovation__text">Nemo enim ipsam voluptatem quia voluptas sit aspernatur aut odit aut fugit, sed quia consequuntur magni dolores eos qui ratione voluptatem sequi nesciunt. Neque porro quisquam est, qui dolorem ipsum quia dolor sit amet, consectetur, adipisci velit, sed quia non numquam eius modi tempora incidunt ut labore</p>
  <ul class="abs checks">
    <li>Duis aute irure dolor in reprehenderit in voluptate</li>
    <li>Neque porro quisquam est, qui dolorem</li>
    <li>Quis autem vel eum iure reprehenderit</li>
    <li>But I must explain to you how all</li>
  </ul>
</section>

<section class="notify">
  <h2 class="abs notify__title pixel">Get Notified of Any Updates!</h2>
  <p class="abs notify__lead">Duis sed odio sit amet nibh vulputate cursus a sit amet mauris. Morbi accumsan ipsum velit. Nam nec tellus a odio tincidunt auctor a ornare odio. Sed non mauris</p>
  <div class="abs notify__field">
    <svg width="24" height="16" viewBox="0 0 24 16"><rect x="1" y="1" width="22" height="14" fill="none" stroke="#ccc" stroke-width="1.5"/><path d="M1 1l11 8 11-8" fill="none" stroke="#ccc" stroke-width="1.5"/></svg>
    <span>Enter Your E-mail Adress</span>
  </div>
  <a class="btn btn--solid notify__btn">Sign-up Now</a>
</section>

<section class="reviews">
  <h2 class="sec-title pixel reviews__title">Customer <em>Reviews</em></h2>
  <article class="review" style="left:98px">
    <div class="review__avatar" role="img" aria-label="Customer portrait"></div>
    <div class="review__body">
      <q>Lorem ipsum dolor sit amet, consectetur adipiscing elit, sed do eiusmod tempor incididunt ut labore et dolore magna aliqua. Ut enim ad minim veniam, quis nostrud</q>
      <div class="review__stars">★★★<span>☆☆</span></div>
      <div class="review__name">JOHN DOE</div>
    </div>
  </article>
  <article class="review" style="left:644px">
    <div class="review__avatar" role="img" aria-label="Customer portrait"></div>
    <div class="review__body">
      <q>Lorem ipsum dolor sit amet, consectetur adipiscing elit, sed do eiusmod tempor incididunt ut labore et dolore magna aliqua. Ut enim ad minim veniam, quis nostrud</q>
      <div class="review__stars">★★★<span>☆☆</span></div>
      <div class="review__name">JOHN DOE</div>
    </div>
  </article>
</section>

<footer class="footer">
  <div class="abs social">
    <i aria-label="plimber"></i><i aria-label="vendoloop"></i><i aria-label="mirtavel"></i><i aria-label="trelvanet"></i>
  </div>
  <nav class="abs footer__nav">Home / About Us / Our Services / Reviews / Contact Us</nav>
  <p class="abs footer__copy">2016 © Copyrights Kolvarin.All Rights Reserved</p>
</footer>

</body>
</html>
```